TALMORK

The business want a professional looking business card. We have a scetch we will add but want the extra upgrade, and would like more suggestions for variations of our business cards.

```html
<!DOCTYPE html>
<html lang="en">
<head>
<meta charset="utf-8">
<title>TALMORK – Business Card</title>
<link rel="stylesheet" href="https://fonts.googleapis.com/css2?family=Abril+Fatface&family=Cinzel:wght@700&family=Open+Sans:wght@400&family=Lato:wght@700&display=swap">
<style>
  :root {
    --backdrop: #8f8f8f;
    --card-black: #050505;
    --card-mid: #1f1f1f;
    --gold: #d9b04a;
    --gold-light: #f2d98a;
    --gold-deep: #8c6a22;
    --text-soft: #e6e6e6;
  }
  * { margin: 0; padding: 0; box-sizing: border-box; }
  html, body { width: 1200px; height: 1200px; overflow: hidden; }
  body { background: var(--backdrop); position: relative; font-family: "Open Sans", sans-serif; }

  .card {
    position: absolute;
    left: 281px;
    width: 642px;
    height: 366px;
    background: linear-gradient(180deg, var(--card-black) 0%, var(--card-mid) 50%, var(--card-black) 100%);
    overflow: hidden;
  }
  .card--front { top: 195px; }
  .card--back { top: 639px; }

  .pattern-frame { position: absolute; inset: 0; width: 642px; height: 366px; }

  .front-content {
    position: absolute; inset: 0;
    text-align: center;
  }
  .holder-name {
    position: absolute; top: 96px; left: 0; right: 0;
    font-family: "Abril Fatface", serif;
    font-size: 27px;
    color: var(--gold);
    letter-spacing: 0.3px;
  }
  .holder-role {
    position: absolute; top: 131px; left: 0; right: 0;
    font-size: 14.5px;
    color: var(--text-soft);
  }
  .contact-divider {
    position: absolute; top: 166px; left: 0; right: 0;
    display: flex; justify-content: center; align-items: center; gap: 8px;
  }
  .contact-divider .rule { width: 55px; height: 1.5px; background: var(--gold); }
  .contact-divider .rule--left { margin-right: 4px; }
  .contact-divider .rule--right { margin-left: 4px; }
  .contact-list {
    position: absolute; top: 196px; left: 0; right: 0;
    list-style: none;
    font-size: 13.5px;
    line-height: 21px;
    color: var(--text-soft);
  }

  .back-content {
    position: absolute; left: 0; right: 0; top: 138px;
    text-align: center;
  }
  .brand-name {
    font-family: "Cinzel", serif;
    font-weight: 700;
    font-size: 46px;
    letter-spacing: 2px;
    color: var(--gold);
    line-height: 1;
  }
  .brand-since {
    margin-top: 14px;
    font-family: "Lato", sans-serif;
    font-weight: 700;
    font-size: 12.5px;
    letter-spacing: 6px;
    color: var(--gold);
  }
</style>
</head>
<body>

  <section class="card card--front">
    <svg class="pattern-frame" viewBox="0 0 642 366" role="img" aria-label="Gold floral ornament pattern bordering the card">
      <defs>
        <linearGradient id="ornamentTone" x1="0" y1="0" x2="1" y2="1">
          <stop offset="0" stop-color="#8a6b2a"/>
          <stop offset="0.5" stop-color="#5e4818"/>
          <stop offset="1" stop-color="#8a6b2a"/>
        </linearGradient>
      </defs>
      <path fill="url(#ornamentTone)" fill-rule="evenodd"
        d="M0 0H642V366H0Z M62 66H580V300H62Z"/>
    </svg>

    <div class="front-content">
      <h1 class="holder-name">Arne Solvik Haugen</h1>
      <p class="holder-role">CEO &amp; Founder</p>
      <div class="contact-divider">
        <span class="rule rule--left"></span>
        <svg width="16" height="16" viewBox="0 0 16 16" aria-hidden="true">
          <path fill="var(--gold)" d="M4 2l2.2 2.6-1.2 1.6c.8 1.8 2 3 3.8 3.8l1.6-1.2L13 11l-1.4 2c-4.6-.4-8.2-4-8.6-8.6z"/>
        </svg>
        <svg width="18" height="14" viewBox="0 0 18 14" aria-hidden="true">
          <rect x="1" y="2" width="16" height="10" fill="var(--gold)"/>
          <path d="M1 2l8 6 8-6" fill="none" stroke="#1a1a1a" stroke-width="1.2"/>
        </svg>
        <svg width="16" height="16" viewBox="0 0 16 16" aria-hidden="true">
          <circle cx="8" cy="8" r="7" fill="var(--gold)"/>
          <path d="M1 8h14M8 1c-3 3-3 11 0 14M8 1c3 3 3 11 0 14" fill="none" stroke="#1a1a1a" stroke-width="1"/>
        </svg>
        <span class="rule rule--right"></span>
      </div>
      <ul class="contact-list">
        <li>004791234567</li>
        <li>talmork.llc@mailbox.com</li>
        <li>www.talmork.llc</li>
      </ul>
    </div>
  </section>

  <section class="card card--back">
    <div class="back-content">
      <h2 class="brand-name">TALMORK</h2>
      <p class="brand-since">SINCE 2026</p>
    </div>
  </section>

</body>
</html>
```